Vernac Law Business cards and stationary design project

We are looking for a stationary design for business cards (double sided), 8x10, 5x7, and legal and standard envelopes.

We would like the design to match the logo that we have already.
Color palate preferred is Teal, White, grey and any others that will look good for a professional law firm.

We would like this statement: "RELATIONSHIPS. RESPECT. RESULT" to be on the back of the business cards and maybe on the stationary if it looks good.

Please see link to website for more information: www.vernac-law.example

Target Market(s)

Potential clients that need Attorney services.

Industry/Entity Type

Law Firm

Contact Information for Business Card

We would like the front and back to be two different colors. Current business cards are teal front, grey back and are a vertical design. We are open to options with colors.

Font styles to use
Serif

Colors
33a6d7
33b8a4
b9b9b9
5c5c5c

Requirements
Must have
• Logo supplied needs to go on the card and stationary.
• Match website color palate, www.vernac-law.example
• Be professional and not too wordy.
• Criminal Law, Civil Litigation, Personal Injury, Restraining Orders need to be on the card.
Nice to have
• RELATIONSHIPS. RESPECT. RESULTS. on the back of the card.
Should not have
• Not be too busy/wordy or too flashy.

```html
<!DOCTYPE html>
<html lang="en">
<head>
<meta charset="utf-8">
<title>Vernac Law – Business Card</title>
<link rel="stylesheet" href="https://fonts.googleapis.com/css2?family=Cinzel:wght@400;500&family=Tinos&display=swap">
<style>
  :root {
    --backdrop: #3b3b3b;
    --paper: #ffffff;
    --teal: #11879a;
    --teal-text: #138a9c;
    --ink: #4a4a4a;
    --on-teal: #ffffff;
  }
  * { margin: 0; padding: 0; box-sizing: border-box; }
  html, body {
    width: 1105px;
    height: 1200px;
    overflow: hidden;
    background: var(--backdrop);
  }
  .card {
    position: absolute;
    left: 192px;
    width: 720px;
    height: 412px;
    text-align: center;
  }
  .card--front { top: 146px; background: var(--paper); }
  .card--back  { top: 602px; background: var(--teal); }

  .line { position: absolute; left: 0; right: 0; }

  .person-name {
    top: 68px;
    font-family: "Cinzel", serif;
    font-size: 31px;
    font-weight: 500;
    color: var(--teal-text);
    letter-spacing: 1px;
  }
  .person-title {
    top: 109px;
    font-family: "Cinzel", serif;
    font-size: 21px;
    color: var(--ink);
    letter-spacing: 1px;
  }
  .divider {
    position: absolute;
    left: 158px;
    width: 404px;
    border-top: 2px dotted var(--teal-text);
  }
  .divider--top { top: 152px; }
  .divider--bottom { top: 250px; }

  .contact {
    font-family: "Tinos", serif;
    font-size: 19px;
    color: var(--ink);
  }
  .contact b { color: var(--teal-text); font-weight: 700; }
  .contact--phone { top: 174px; }
  .contact--web { top: 204px; }

  .practice {
    font-family: "Tinos", serif;
    font-size: 19px;
    color: var(--ink);
  }
  .practice--primary { top: 267px; }
  .practice--secondary { top: 293px; }

  .tagline {
    top: 322px;
    font-family: "Cinzel", serif;
    font-size: 21px;
    color: var(--teal-text);
    letter-spacing: 0.5px;
  }

  .firm-name {
    top: 180px;
    font-family: "Cinzel", serif;
    font-size: 40px;
    color: var(--on-teal);
    letter-spacing: 2px;
  }
</style>
</head>
<body>
  <section class="card card--front">
    <p class="line person-name">Maren Vernac</p>
    <p class="line person-title">Trial Lawyer</p>
    <div class="divider divider--top"></div>
    <p class="line contact contact--phone"><b>P:</b> (555) 014-2368&nbsp; <b>E:</b> maren@vernac-law.example</p>
    <p class="line contact contact--web"><b>W:</b> www.vernac-law.example</p>
    <div class="divider divider--bottom"></div>
    <p class="line practice practice--primary">Criminal Law</p>
    <p class="line practice practice--secondary">Civil Litigation/Personal Injury, Restraining</p>
    <p class="line tagline">Relationships. Respect. Results.</p>
  </section>

  <section class="card card--back">
    <p class="line firm-name">Vernac Law</p>
  </section>
</body>
</html>
```